indépendant en tant que Massothérapeute et Préparateur Mental, j'ai besoin de ...

Massothérapeute et préparateur mental indépendant, je recherche une carte de visite sobre et dynamique, sans images liées au massage ou à la préparation mentale mais intégrant mon logo. Les couleurs que j'aime bien sont : Blanc, gris, anthracite, noir et jaune

Contact Information for Business Card

carte de préférence Horizontale
neutre qui puisse toucher le deux domaines Massothérapie et préparation mentale

Requirements
Must have
• mon projet doit intégrer au recto:
LOGO
Loïc Bardèze
078 513 26 48
info@loicbardeze.ch
et éventuellement www.loicbardeze.ch

et au verso les deux adresses:

Chemin des Ormilles 7B
1400 Yverdon-les-Bains

Route de la Gravière 9
1736 Grandmont

Should not have
• mon projet ne doit pas contenir d'image en liens avec le massage ni la préparation mentale.

```html
<!DOCTYPE html>
<html lang="fr">
<head>
<meta charset="utf-8">
<title>Loïc Bardèze – Carte de visite</title>
<link rel="stylesheet" href="https://fonts.googleapis.com/css2?family=Rubik:wght@400;500&display=swap">
<style>
  :root {
    --backdrop: #8c8c8c;
    --anthracite: #231f20;
    --paper: #ffffff;
    --ink-light: #ffffff;
    --ink-dark: #231f20;
    --metal: #9a9396;
  }
  * { margin: 0; padding: 0; box-sizing: border-box; }
  html, body {
    width: 1200px; height: 1200px; overflow: hidden;
    background: var(--backdrop);
    font-family: "Rubik", Arial, sans-serif;
  }
  .stage { position: relative; width: 1200px; height: 1200px; }
  .card {
    position: absolute;
    left: 257px;
    width: 800px; height: 457px;
    border-radius: 26px;
    overflow: hidden;
    transform-origin: 0 0;
    transform: scale(0.8575);
  }
  .card--front { top: 165px; background: var(--paper); }
  .card--back { top: 653px; background: var(--anthracite); }
  .front-panel { position: absolute; inset: 0; width: 800px; height: 457px; }
  .front-panel path { fill: var(--anthracite); }

  .contact { position: absolute; left: 48px; top: 198px; color: var(--ink-light); }
  .contact__name { font-size: 24px; font-weight: 500; line-height: 30px; }
  .contact__address { margin-top: 14px; margin-left: 5px; font-size: 17px; font-weight: 500; line-height: 22px; }
  .contact__address + .contact__address { margin-top: 7px; }
  .contact__lines { list-style: none; margin-top: 8px; margin-left: 5px; font-size: 17px; font-weight: 500; }
  .contact__lines li { display: flex; align-items: center; height: 23px; }
  .contact__lines svg { width: 15px; height: 15px; margin-right: 11px; fill: var(--ink-light); }

  .brand { position: absolute; display: flex; align-items: center; gap: 12px; font-weight: 500; }
  .brand__dot { width: 14px; height: 14px; border-radius: 50%; }
  .card--front .brand { right: 58px; top: 96px; font-size: 30px; color: var(--ink-dark); }
  .card--front .brand__dot { background: var(--ink-dark); }
  .card--back .brand { left: 0; right: 0; top: 196px; justify-content: center; font-size: 42px; color: var(--metal); }
  .card--back .brand__dot { background: var(--metal); width: 18px; height: 18px; }
</style>
</head>
<body>
<main class="stage">
  <section class="card card--front" aria-label="Recto">
    <svg class="front-panel" viewBox="0 0 800 457" aria-hidden="true">
      <path d="M0 0 H222 Q240 0 250 16 L502 457 H0 Z"/>
    </svg>
    <div class="brand"><span class="brand__dot"></span><span class="brand__name">Loïc Bardèze</span></div>
    <div class="contact">
      <p class="contact__name">Loïc Bardèze</p>
      <p class="contact__address">Chemin des Ormilles 7B<br>1412 Valmont-les-Prés</p>
      <p class="contact__address">Route de la Gravière 9<br>1736 Grandmont</p>
      <ul class="contact__lines">
        <li><svg viewBox="0 0 24 24"><path d="M6.6 10.8a15.2 15.2 0 0 0 6.6 6.6l2.2-2.2a1 1 0 0 1 1-.25 11.4 11.4 0 0 0 3.6.57 1 1 0 0 1 1 1V20a1 1 0 0 1-1 1A17 17 0 0 1 3 4a1 1 0 0 1 1-1h3.5a1 1 0 0 1 1 1c0 1.25.2 2.45.57 3.57a1 1 0 0 1-.25 1z"/></svg>078 513 26 48</li>
        <li><svg viewBox="0 0 24 24"><path d="M2 5h20v14H2z M2 5l10 8 10-8" fill="none" stroke="#fff" stroke-width="2.4"/></svg>info@loicbardeze.ch</li>
        <li><svg viewBox="0 0 24 24"><circle cx="12" cy="12" r="10"/><path d="M7 8c2 0 3 1 3 3s-2 2-2 4M15 5c0 2 2 2 2 4s-2 2-3 3 1 3 2 4" fill="none" stroke="#231f20" stroke-width="2"/></svg>www.loicbardeze.ch</li>
      </ul>
    </div>
  </section>

  <section class="card card--back" aria-label="Verso">
    <div class="brand"><span class="brand__dot"></span><span class="brand__name">Loïc Bardèze</span></div>
  </section>
</main>
</body>
</html>
```